Website Design Request - Management Consulting Firm

We need a Website designed for an IT Management Staffing and Recruiting firm called TRAVENOK based in San Francisco.

The firm is an high-end technology staffing agency. Our focus is on quality and high-caliber candidates rather than quantity.

The website will have two main home pages. One for the recruiter and another on for the candidates.

The website needs to optimize for mobile devices as well.

I have attached few mock-ups that I have done just to show what I am thinking. The UI needs to be very clean, fluid, and it needs to have a modern, rustic, professional feel to it.

Target Market(s)

Technology Manager, Director, VP, CIO of Companies that have $4b-10b dollar revenue. Such as larkspurdwellings.example , https://www.velmorian.example/, quillnet.example, zib.example

Industry/Entity Type

Management Consulting

Number of Pages Required

5+ page

Font styles to use
Sans Serif

Colors
f37122
ffffff

Requirements
Must have
• Please review mock-ups for suggestions
Nice to have
Should not have

```html
<!DOCTYPE html>
<html lang="en">
<head>
<meta charset="utf-8">
<title>TRAVENOK – IT Project Management Jobs</title>
<link rel="stylesheet" href="https://fonts.googleapis.com/css2?family=Open+Sans:wght@300;400;600&display=swap">
<style>
:root{
  --orange:#f37122;
  --white:#ffffff;
  --ink:#2f2f2f;
  --muted:#555555;
  --footer-bg:#ebebe3;
  --rule:#d6d6cc;
  --why:#f9b98f;
}
*{box-sizing:border-box;margin:0;padding:0}
html,body{width:926px;height:1200px;overflow:hidden;background:var(--white)}
body{font-family:"Open Sans",Arial,sans-serif;color:var(--ink);position:relative}
.abs{position:absolute}
a{color:inherit;text-decoration:none}

/* header */
.site-header{left:0;top:0;width:926px;height:83px;background:var(--white);box-shadow:0 2px 4px rgba(0,0,0,.25);z-index:2}
.brand{left:102px;top:16px;font-size:40px;font-weight:400;color:var(--orange);letter-spacing:2px;line-height:44px}
.main-nav a{position:absolute;top:37px;font-size:10px;color:#333}

/* hero */
.hero{left:0;top:83px;width:926px;height:356px}
.hero-photo{position:absolute;inset:0;background:radial-gradient(ellipse at 50% 45%,#e9eef1 0%,#b9c8d0 45%,#6f8a98 100%)}
.hero-title{left:0;top:163px;width:926px;text-align:center;font-size:31px;font-weight:400;color:#333}
.hero-sub{left:0;top:219px;width:926px;text-align:center;font-size:12px;color:#333}
.email-field{left:275px;top:260px;width:376px;height:30px;border:2px solid #222;background:var(--white);font-size:8px;padding:9px 11px;color:#333}
.cta{left:402px;top:314px;width:122px;height:28px;background:var(--orange);color:var(--white);border-radius:2px;font-size:10px;text-align:center;line-height:28px}
.employer-note{left:0;top:379px;width:926px;text-align:center;font-size:7.5px;color:#222}
.employer-note a{text-decoration:underline}

/* tabs band */
.tab-band{left:0;top:439px;width:926px;height:71px;background:var(--orange)}
.tab{top:23px;font-size:18px;font-weight:400}
.tab.active{left:295px;color:var(--white)}
.tab.muted{left:486px;color:var(--why)}

/* steps */
.steps-title{left:0;top:541px;width:926px;text-align:center;font-size:19px;color:#333}
.steps-lead{left:0;top:583px;width:926px;text-align:center;font-size:11.5px;color:#333}
.timeline{left:337px;top:637px}
.step-title{left:373px;font-size:19px;color:#333}
.step-text{left:374px;font-size:11.5px;color:#333;line-height:18px;width:300px}
.upload-link{left:398px;top:889px;font-size:12px;color:#333}
.upload-link svg{vertical-align:-1px;margin-right:9px}

/* footer */
.site-footer{left:0;top:949px;width:926px;height:251px;background:var(--footer-bg)}
.footer-brand{left:102px;top:977px;font-size:30px;color:var(--orange);letter-spacing:2px;line-height:34px}
.social{left:100px;top:1034px;display:flex;gap:5px}
.social span{width:24px;height:24px;border:1.5px solid #555;border-radius:50%;display:block}
.footer-heading{font-size:15px;color:#333;font-weight:400}
.quick-links{left:310px;top:975px}
.quick-links ul{list-style:none;margin-top:10px}
.quick-links li{font-size:8px;color:#555;line-height:18.5px}
.contact{left:468px;top:975px}
.contact ul{list-style:none;margin-top:12px}
.contact li{display:flex;gap:9px;font-size:7.5px;color:#444;margin-bottom:10px;line-height:10px}
.contact svg{flex:none}
.subscribe{left:638px;top:982px}
.subscribe p{font-size:7.5px;color:#444;line-height:18px;margin:16px 0 0 3px;width:190px}
.sub-field{left:641px;top:1065px;width:183px;height:26px;background:var(--white);border:1px solid #ccc;font-size:7.5px;padding:8px 9px;color:#333}
.sub-btn{left:642px;top:1106px;width:64px;height:23px;border:1px solid #222;border-radius:2px;font-size:8px;text-align:center;line-height:21px;color:#222}
.footer-rule{left:0;top:1156px;width:926px;height:1px;background:var(--rule)}
.copyright{left:0;top:1174px;width:926px;text-align:center;font-size:7.5px;color:#555}
</style>
</head>
<body>

<header class="site-header abs">
  <div class="brand abs">TRAVENOK</div>
  <nav class="main-nav">
    <a href="#" style="left:553px">Professional</a>
    <a href="#" style="left:643px">Employers</a>
    <a href="#" style="left:726px">Sign In</a>
    <a href="#" style="left:793px">Sign Up</a>
  </nav>
</header>

<section class="hero abs">
  <div class="hero-photo" role="img" aria-label="Professionals in floating glass panels above an open hand, soft blue-grey backdrop"></div>
</section>
<h1 class="hero-title abs">Looking for IT Projects Management Jobs?</h1>
<p class="hero-sub abs">Upload your resume, accept interview requests, get offers</p>
<div class="email-field abs">Your Email Address</div>
<a class="cta abs" href="#">Get offers Now</a>
<p class="employer-note abs">Looking for talents? <a href="#">see how it works for employers</a></p>

<div class="tab-band abs">
  <span class="tab active abs">How it Works?</span>
  <span class="tab muted abs">Why Us?</span>
</div>

<h2 class="steps-title abs" style="font-weight:400">3 Simple Steps</h2>
<p class="steps-lead abs">Employers pay 25% more for a better FIT Project Manager</p>

<svg class="timeline abs" width="26" height="200" viewBox="0 0 26 200" aria-hidden="true">
  <line x1="12" y1="23" x2="12" y2="71" stroke="#f37122" stroke-width="3"/>
  <line x1="12" y1="97" x2="12" y2="165" stroke="#f37122" stroke-width="3"/>
  <circle cx="12" cy="12" r="10" fill="#fff" stroke="#f37122" stroke-width="2.5"/>
  <circle cx="12" cy="86" r="10" fill="#fff" stroke="#f37122" stroke-width="2.5"/>
  <circle cx="12" cy="180" r="10" fill="#fff" stroke="#f37122" stroke-width="2.5"/>
</svg>

<h3 class="step-title abs" style="top:634px;font-weight:400">Upload Your resume</h3>
<p class="step-text abs" style="top:665px">answer few questions and upload your resume</p>
<h3 class="step-title abs" style="top:708px;font-weight:400">We send you interview Requests</h3>
<p class="step-text abs" style="top:739px">Interested in someone? with a single click, send interview request and let us handle the rest.</p>
<h3 class="step-title abs" style="top:801px;font-weight:400">Get $1000 Bonus</h3>
<p class="step-text abs" style="top:832px">Find a Job and get $1000 bonus Travenok</p>

<a class="upload-link abs" href="#"><svg width="11" height="11" viewBox="0 0 11 11" aria-hidden="true"><path d="M4 0h3v4h2.5L5.5 8 1.5 4H4z" fill="#f37122"/><rect x="0" y="9" width="11" height="2" fill="#f37122"/></svg>Upload Your Resume</a>

<footer class="site-footer abs"></footer>
<div class="footer-brand abs">TRAVENOK</div>
<div class="social abs" aria-label="Social links"><span></span><span></span><span></span><span></span><span></span></div>

<div class="quick-links abs">
  <h4 class="footer-heading">QUICK LINKS</h4>
  <ul><li>Professional</li><li>Employers</li><li>Sign In</li><li>Sign Up</li></ul>
</div>

<div class="contact abs">
  <h4 class="footer-heading">CONTACT US</h4>
  <ul>
    <li><svg width="10" height="9" viewBox="0 0 10 9"><path d="M0 2.5C0 1 2 0 5 0s5 1 5 2.5V4H7V3H3v1H0z M1.5 4.5h7L9.5 9h-9z" fill="#555"/></svg>555-014-7410/</li>
    <li><svg width="10" height="9" viewBox="0 0 10 9"><rect x="2" y="0" width="6" height="3" fill="#555"/><rect x="0" y="3" width="10" height="4" fill="#555"/><rect x="2" y="6" width="6" height="3" fill="#777"/></svg>555-019-0604</li>
    <li><svg width="10" height="8" viewBox="0 0 10 8"><rect x=".5" y=".5" width="9" height="7" fill="none" stroke="#555"/><path d="M.5 .5 5 4.5 9.5 .5" fill="none" stroke="#555"/></svg><span style="text-decoration:underline">info@travenok.example</span></li>
    <li><svg width="10" height="11" viewBox="0 0 10 11"><path d="M5 0a4 4 0 0 1 4 4c0 3-4 7-4 7S1 7 1 4a4 4 0 0 1 4-4z" fill="#555"/><circle cx="5" cy="4" r="1.5" fill="#ebebe3"/></svg>#2868 Lorem ipsum dolor sit<br>amet, consectetur</li>
  </ul>
</div>

<div class="subscribe abs">
  <h4 class="footer-heading">SUBSCRIBE NEWSLETTER</h4>
  <p>Enter your email address to receive the latest news our blog.</p>
</div>
<div class="sub-field abs">Email Id</div>
<div class="sub-btn abs">SUBSCRIBE</div>

<div class="footer-rule abs"></div>
<p class="copyright abs">©2016 travenoktech.example. All Rights Reserved.</p>

</body>
</html>
```